Thoroughbred Racing Partnership needs web design

Glimmer of Laurel Partners is a management group who buys horses and races them on both the West and East coasts. The premise of the business is for an investment as little as $500, anyone can be a partner and own a percentage of a horse(s). This is a low cost way of getting involved in the exciting sport of Thoroughbred Racing, without shouldering the heavy financial responsibility. Our target market is mostly males 40+ but we want to include all target markets. We are looking for something very clean and professional, we want to give an image of success. Nothing overly "artsy." I have included the logo in which you can incorporate in the site. Also, the logo colors will be the colors of our "silks." The silks are what the jockey wears and will be an important marketing tool for GOL. We would like a very prominent picture of a racehorse somewhere on the homepage, we want to make it clear that is a website for Horseracing partnerships.

On the top of the site, it should say "Glimmer of Laurel" (on the top)
and below that "Thoroughbred Racing Partnerships." (below that)

The main sections, which should be across the top are:

Home
About Us
Ownership
Stable Roster
News
Contact us

Some of these will have drop down menus.

An example of a competitor website that we like is: www.harrowgatefarm.example
An example of a competitor website that we don't like is: www.paddockvue.example
Updates

Project Deadline Extended
Reason: We have a Board of Directors meeting on the 22nd and we will be making a decision on that day. I'm giving an extension so that all designers are able to submit their designs by the 22nd. Thank you!

Target Market(s)

40+ males

Industry/Entity Type

Business

Requirements
Must have
• our logo must be on the site. We would like at least one bold image of a thoroughbred horse in action. The picture is going to tell the story so it needs to be very eye-catching.

Our slogan should also be included on the website, "Experience the thrill of owning a Racehorse."
Should not have
• cartoons, artsy pictures, pictures of Steeplechase horses or "jumpers." This partnership is for racehorses only, there is not jumping involved with the horses.

```html
<!DOCTYPE html>
<html lang="en">
<head>
<meta charset="utf-8">
<title>Glimmer of Laurel – Thoroughbred Racing Partnerships</title>
<link rel="stylesheet" href="https://fonts.googleapis.com/css2?family=Arvo:ital,wght@0,400;0,700;1,700&family=Open+Sans:wght@400;600;700&display=swap">
<style>
:root{
  --ink:#141414;
  --charcoal:#1d1d1d;
  --panel:#262626;
  --panel-head:#111111;
  --line:#3a3a3a;
  --orange:#e5a11c;
  --orange-dark:#c4850d;
  --text:#ffffff;
  --muted:#a9a9a9;
  --dim:#7a7a7a;
}
*{box-sizing:border-box;margin:0;padding:0}
html,body{width:1200px;height:2344px;overflow:hidden}
body{
  font-family:"Open Sans",Arial,sans-serif;color:var(--text);
  background:
    radial-gradient(ellipse 700px 520px at 600px 700px,#5a5a58 0%,rgba(60,60,58,.4) 45%,transparent 75%),
    radial-gradient(ellipse 900px 600px at 600px 1500px,#2e2e2c 0%,transparent 70%),
    var(--ink);
}
.page{position:relative;width:1200px;height:2344px}
.abs{position:absolute}

/* header */
.brand{left:22px;top:12px;display:flex;align-items:center;gap:10px}
.brand-mark{width:26px;height:26px;background:var(--orange)}
.brand-name{font:700 22px/1 "Open Sans",sans-serif;letter-spacing:1px;color:var(--text);white-space:nowrap}
.topline{left:250px;top:18px;font-size:11px;line-height:14px;color:var(--muted);white-space:nowrap}
.socials{right:24px;top:12px;display:flex;gap:6px}
.socials span{width:18px;height:18px;background:#4a4a4a}
.site-title{right:24px;top:40px;text-align:right}
.site-title h1{font:italic 700 40px/1 Arvo,serif;color:var(--text)}
.site-title p{font:400 22px/1.2 "Open Sans",sans-serif;color:var(--orange);margin-top:6px}
.nav{left:22px;top:56px;display:flex}
.nav a{display:block;padding:0 18px;height:34px;line-height:34px;font-size:14px;font-weight:600;color:var(--text);text-decoration:none;background:#2a2a2a;border-right:1px solid #000}
.nav a.active{background:var(--orange)}

/* slider */
.slider{left:140px;top:112px;width:920px;height:392px;border:6px solid #0c0c0c}
.slide-photo{width:100%;height:100%;background:linear-gradient(100deg,#3b2d22 0%,#6b5a48 35%,#a89c8a 60%,#4b4d4a 100%)}
.caption{right:24px;top:26px;text-align:right}
.caption .c1{display:inline-block;background:var(--orange);font:700 28px/1 "Open Sans",sans-serif;padding:10px 16px}
.caption .c2{display:block;background:rgba(0,0,0,.75);font:400 26px/1 "Open Sans",sans-serif;padding:9px 16px;margin-top:4px}
.arrow{top:172px;width:34px;height:34px;border-radius:50%;background:rgba(0,0,0,.75);display:flex;align-items:center;justify-content:center}
.arrow.left{left:10px}.arrow.right{right:10px}

/* slogan */
.slogan{left:0;top:566px;width:1200px;text-align:center}
.slogan h2{font:700 38px/1.2 Arvo,serif;letter-spacing:1px}
.slogan p{font:400 30px/1.3 "Open Sans",sans-serif;color:#dcdcdc;margin-top:14px}
.slogan p em{font-style:normal;color:var(--orange)}
.btn-orange{display:inline-flex;align-items:center;gap:12px;background:var(--orange);color:var(--text);font:600 30px/1 "Open Sans",sans-serif;padding:10px 38px;margin-top:20px;border:0}

/* feature boxes */
.features{left:20px;top:862px;width:1160px;display:flex;gap:10px}
.feature{flex:1;background:rgba(20,20,20,.85);height:190px}
.feature-head{display:flex;align-items:center;gap:10px;height:48px;padding:0 14px;background:var(--panel-head);font:400 24px/1 Arvo,serif}
.feature p{font-size:11px;line-height:1.55;color:var(--muted);padding:12px 14px 0}
.read-more{display:inline-flex;align-items:center;gap:6px;background:#0a0a0a;border:1px solid var(--line);color:var(--text);font-size:11px;padding:5px 10px;margin:14px 14px 0}

/* about */
.video{left:48px;top:1080px;width:432px;height:232px;background:#000}
.video-photo{width:100%;height:206px;background:linear-gradient(160deg,#8d8f7c 0%,#6e6a52 45%,#4b3b2a 100%)}
.play{left:186px;top:72px;width:60px;height:56px;border-radius:10px;background:rgba(0,0,0,.8);display:flex;align-items:center;justify-content:center}
.video-bar{height:26px;display:flex;align-items:center;gap:10px;padding:0 10px}
.video-bar i{flex:1;height:3px;background:#444}
.about{left:620px;top:1128px;width:560px}
.about h3{font:700 30px/1 "Open Sans",sans-serif;text-align:right}
.about p{font-size:12px;line-height:1.6;color:var(--muted);margin-top:12px}
.about .btn-small{float:right}
.btn-small{display:inline-flex;align-items:center;gap:8px;background:var(--orange);font-size:16px;padding:7px 22px;margin-top:8px}

/* horses */
.horses{left:20px;top:1354px;width:1160px}
.horses h3{font:700 30px/1 Arvo,serif;color:var(--orange)}
.horses p{font-size:12px;color:var(--muted);margin-top:8px}
.strip{left:0;top:1448px;width:1200px;height:216px;display:flex;gap:6px;padding:0 20px}
.strip div{flex:1}
.tag{left:20px;top:1432px;width:56px;height:16px;background:var(--orange)}

/* testimonial */
.testimonial{left:0;top:1720px;width:1200px;height:180px;background:rgba(10,10,10,.55);padding:24px 34px}
.testimonial h3{font:700 30px/1 "Open Sans",sans-serif}
.testimonial .who{font-size:24px;color:var(--orange);margin-top:14px}
.testimonial .who span{font-size:18px;color:var(--text)}
.testimonial p{width:760px;font-size:12px;line-height:1.55;color:var(--muted);margin-top:6px}
.testimonial .btn-small{position:absolute;right:34px;top:110px;font-size:18px;padding:10px 22px}

/* footer */
.footer{left:0;top:1960px;width:1200px;height:352px;background:rgba(8,8,8,.7);padding:26px 20px;display:flex;gap:40px}
.fcol{width:260px}
.fcol h4{font:600 18px/1 "Open Sans",sans-serif;margin-bottom:18px}
.tweet{display:flex;gap:10px;margin-bottom:22px}
.tweet i{width:16px;height:16px;border-radius:50%;background:#5a5a5a;flex:none;margin-top:2px}
.tweet p{font-size:11px;line-height:1.5;color:var(--muted)}
.album{display:grid;grid-template-columns:repeat(4,50px);gap:6px}
.album div{height:42px}
.contact-line{font-size:11px;line-height:1.7;color:var(--muted)}
.phone{display:flex;align-items:center;gap:10px;margin-top:20px;font:700 30px/1 "Open Sans",sans-serif;color:var(--orange)}
.fsocial{display:flex;gap:6px;margin-top:14px}
.fsocial span{width:18px;height:18px;background:#4a4a4a}
.form .row{display:flex;gap:8px}
.form .field{flex:1;height:24px;background:#f2f2f2;color:#777;font-size:11px;padding:5px 8px}
.form .area{height:90px;margin-top:8px}
.form .submit{float:right;margin-top:8px;background:#0a0a0a;border:1px solid var(--line);font-size:12px;padding:5px 14px;display:flex;gap:6px;align-items:center}
.bottom{left:0;top:2312px;width:1200px;height:32px;background:#070707;display:flex;justify-content:space-between;align-items:center;padding:0 20px;font-size:11px;color:var(--dim)}
</style>
</head>
<body>
<div class="page">

  <header>
    <div class="abs brand"><span class="brand-mark"></span><span class="brand-name">GOL PARTNERS</span></div>
    <div class="abs topline">12 Paddock Row, Ocala FL &nbsp;|&nbsp; 555 010 0199</div>
    <div class="abs socials"><span></span><span></span><span></span><span></span></div>
    <div class="abs site-title">
      <h1>Glimmer of Laurel</h1>
      <p>Thoroughbred Racing Partnerships</p>
    </div>
    <nav class="abs nav">
      <a class="active" href="#">Home</a><a href="#">About Us</a><a href="#">Ownership</a><a href="#">Stable Roster</a><a href="#">News</a><a href="#">Contact</a>
    </nav>
  </header>

  <section class="abs slider">
    <div class="slide-photo" role="img" aria-label="Jockey in silks riding a thoroughbred racehorse at full gallop"></div>
    <div class="abs caption"><span class="c1">Lorem ipsum dolor</span><span class="c2">Sed ut perspiciatis</span></div>
    <div class="abs arrow left"><svg width="12" height="14"><path d="M9 1L3 7l6 6" stroke="#fff" stroke-width="2.5" fill="none"/></svg></div>
    <div class="abs arrow right"><svg width="12" height="14"><path d="M3 1l6 6-6 6" stroke="#fff" stroke-width="2.5" fill="none"/></svg></div>
  </section>

  <section class="abs slogan">
    <h2>Experience the thrill of owning a Racehorse</h2>
    <p>Be a part of the thrilling event with just an<br>investment of as little as <em>$500</em></p>
    <span class="btn-orange"><svg width="22" height="18"><path d="M20 9H4M10 2L3 9l7 7" stroke="#fff" stroke-width="3" fill="none"/></svg>Know How</span>
  </section>

  <section class="abs features">
    <div class="feature">
      <div class="feature-head"><svg width="24" height="24"><circle cx="12" cy="8" r="5" fill="#e5a11c"/><path d="M3 23c0-6 4-9 9-9s9 3 9 9z" fill="#e5a11c"/></svg>Ownership</div>
      <p>Lorem ipsum dolor sit amet, consectetur adipiscing elit, sed do eiusmod tempor incididunt ut labore.</p>
      <span class="read-more"><svg width="8" height="8"><path d="M1 0l6 4-6 4z" fill="#fff"/></svg>Read More</span>
    </div>
    <div class="feature">
      <div class="feature-head"><svg width="24" height="24"><path d="M12 2l3 7h7l-6 5 2 8-6-5-6 5 2-8-6-5h7z" fill="#e5a11c"/></svg>Stable Roster</div>
      <p>Lorem ipsum dolor sit amet, consectetur adipiscing elit, sed do eiusmod tempor incididunt ut labore.</p>
      <span class="read-more"><svg width="8" height="8"><path d="M1 0l6 4-6 4z" fill="#fff"/></svg>Read More</span>
    </div>
    <div class="feature">
      <div class="feature-head"><svg width="24" height="24"><rect x="3" y="3" width="18" height="18" fill="#e5a11c"/><path d="M7 8h10M7 12h10M7 16h6" stroke="#111" stroke-width="2"/></svg>News</div>
      <p>Lorem ipsum dolor sit amet, consectetur adipiscing elit, sed do eiusmod tempor incididunt ut labore.</p>
      <span class="read-more"><svg width="8" height="8"><path d="M1 0l6 4-6 4z" fill="#fff"/></svg>Read More</span>
    </div>
    <div class="feature">
      <div class="feature-head"><svg width="24" height="24"><rect x="3" y="5" width="18" height="16" fill="#e5a11c"/><rect x="3" y="5" width="18" height="4" fill="#fff"/><path d="M8 2v5M16 2v5" stroke="#fff" stroke-width="2"/></svg>Events</div>
      <p>Lorem ipsum dolor sit amet, consectetur adipiscing elit, sed do eiusmod tempor incididunt ut labore.</p>
      <span class="read-more"><svg width="8" height="8"><path d="M1 0l6 4-6 4z" fill="#fff"/></svg>Read More</span>
    </div>
  </section>

  <section>
    <div class="abs video">
      <div class="video-photo" role="img" aria-label="Video still of racehorses running on a turf track"></div>
      <div class="abs play"><svg width="20" height="22"><path d="M2 1l17 10L2 21z" fill="#fff"/></svg></div>
      <div class="video-bar"><svg width="10" height="12"><path d="M0 0l10 6-10 6z" fill="#fff"/></svg><i></i><svg width="14" height="12"><path d="M0 4h4l5-4v12l-5-4H0z" fill="#fff"/></svg></div>
    </div>
    <div class="abs about">
      <h3>About Us</h3>
      <p>Lorem ipsum dolor sit amet, consectetur adipiscing elit, sed do eiusmod tempor incididunt ut labore et dolore magna aliqua. Ut enim ad minim veniam, quis nostrud exercitation ullamco laboris nisi ut aliquip ex ea commodo consequat. Duis aute irure dolor in reprehenderit in voluptate velit esse cillum dolore eu fugiat nulla pariatur.</p>
      <span class="btn-small"><svg width="12" height="12"><path d="M1 6h9M6 2l4 4-4 4" stroke="#fff" stroke-width="2" fill="none"/></svg>Read More</span>
    </div>
  </section>

  <section>
    <div class="abs horses">
      <h3>The Horses of Choice</h3>
      <p>Lorem ipsum dolor sit amet, consectetur adipiscing elit, sed do eiusmod tempor incididunt ut labore.</p>
    </div>
    <div class="abs tag"></div>
    <div class="abs strip">
      <div role="img" aria-label="Thoroughbred racing on a dirt track" style="background:linear-gradient(160deg,#8a6a45,#4a3522)"></div>
      <div role="img" aria-label="Horses breaking from the starting gate" style="background:linear-gradient(160deg,#b8b3a6,#6a655a)"></div>
      <div role="img" aria-label="Dark bay racehorse with white blaze" style="background:linear-gradient(160deg,#3d2c20,#7a6a58)"></div>
      <div role="img" aria-label="Racehorse wearing a patterned hood" style="background:linear-gradient(160deg,#8e8c86,#3e3a34)"></div>
      <div role="img" aria-label="Racehorse in the paddock" style="background:linear-gradient(160deg,#6d5540,#2c241c)"></div>
    </div>
  </section>

  <section class="abs testimonial">
    <h3>See what our &nbsp;Partners are saying</h3>
    <div class="who">Martin Hale, <span>CEO, Corvane Inc.</span></div>
    <p>Lorem ipsum dolor sit amet, consectetur adipiscing elit, sed do eiusmod tempor incididunt ut labore et dolore magna aliqua. Ut enim ad minim veniam, quis nostrud exercitation ullamco laboris nisi ut aliquip ex ea commodo consequat.</p>
    <span class="btn-small"><svg width="12" height="12"><path d="M1 6h9M6 2l4 4-4 4" stroke="#fff" stroke-width="2" fill="none"/></svg>View all Testimonials</span>
  </section>

  <footer class="abs footer">
    <div class="fcol">
      <h4>Latest Tweets</h4>
      <div class="tweet"><i></i><p>Lorem ipsum dolor sit amet, new partner filly joins the stable.<br>1 min ago</p></div>
      <div class="tweet"><i></i><p>Lorem ipsum dolor sit amet, race day results posted online.<br>1 hour ago</p></div>
      <div class="tweet"><i></i><p>Lorem ipsum dolor sit amet, open house at the barn Sunday.<br>2 days ago</p></div>
    </div>
    <div class="fcol">
      <h4>Latest Album</h4>
      <div class="album" role="img" aria-label="Grid of race day photo thumbnails">
        <div style="background:#6b5a48"></div><div style="background:#8a8478"></div><div style="background:#4a3a2c"></div><div style="background:#9a8c78"></div>
        <div style="background:#5c5246"></div><div style="background:#7c6a56"></div><div style="background:#3e362e"></div><div style="background:#8c7e6c"></div>
        <div style="background:#a09684"></div><div style="background:#54483c"></div><div style="background:#6e6456"></div><div style="background:#48403a"></div>
      </div>
    </div>
    <div class="fcol">
      <h4>Get In Touch</h4>
      <p class="contact-line">12 Paddock Row, Suite 4<br>Ocala, FL 34470<br>info@glimmeroflaurel.example</p>
      <div class="phone"><svg width="24" height="24"><path d="M6 2l4 5-2 3c1 3 3 5 6 6l3-2 5 4-3 4C10 22 2 14 2 5z" fill="#e5a11c"/></svg>5550100200</div>
      <div class="fsocial"><span></span><span></span><span></span><span></span></div>
    </div>
    <div class="fcol form">
      <h4>Quick Contact</h4>
      <div class="row"><div class="field">Name</div><div class="field">Email</div></div>
      <div class="field area">Message</div>
      <span class="submit"><svg width="8" height="8"><path d="M1 0l6 4-6 4z" fill="#fff"/></svg>Submit</span>
    </div>
  </footer>

  <div class="abs bottom">
    <span>All copyright reserved</span>
    <span>Home &nbsp;About Us &nbsp;Ownership &nbsp;Stable Roster &nbsp;News &nbsp;Contact</span>
  </div>

</div>
</body>
</html>
```